Healthcare and Professional IT Services Company need a redesigned business card

We are a IT Services company that targets small medical practices and professional business such as Attorneys, Accounts, Architects etc. We want to communicate a professional yet friendly image using recent logo redesign here on ArtHarbor. Like to see the colors blue and orange in the design. Must use the Tall Pine Computing as displayed in the new logo - then also want to incorporate the fish logo as well.

Target Market(s)

Small medical and professional services

Industry/Entity Type

It Company

Contact Information for Business Card

The usual stuff, place for name address phone website. Also maybe our tagline which is "rooted in technology"

Requirements
Must have
• My new logo and the fish somewhere on the card

```html
<!DOCTYPE html>
<html lang="en">
<head>
<meta charset="utf-8">
<title>Tall Pine Computing – Business Card</title>
<link rel="stylesheet" href="https://fonts.googleapis.com/css2?family=Open+Sans:ital,wght@0,400;0,600;0,700;1,700&display=swap">
<style>
  :root {
    --stage: #ecebe8;
    --card: #ffffff;
    --brand-blue: #1a8fd6;
    --deep-blue: #1d6fb8;
    --brand-orange: #f39a2b;
    --ink: #1f1f1f;
    --pattern-blue: #dbeaf4;
    --pattern-peach: #f6e3d6;
  }
  * { margin: 0; padding: 0; box-sizing: border-box; }
  html, body {
    width: 1200px; height: 900px; overflow: hidden;
    background: var(--stage);
    font-family: "Open Sans", sans-serif;
    color: var(--ink);
  }
  .canvas { position: relative; width: 1200px; height: 900px; }
  .card {
    position: absolute;
    width: 580px; height: 332px;
    background: var(--card);
    box-shadow: 0 6px 18px rgba(0,0,0,.14);
    overflow: hidden;
  }
  /* Back of card */
  .card-back { left: 120px; top: 110px; }
  .fish-pattern {
    position: absolute; inset: 0;
    background: linear-gradient(135deg, var(--pattern-blue) 0%, #fbfcfd 45%, var(--pattern-peach) 100%);
    opacity: .8;
  }
  .back-wordmark {
    position: absolute; right: 26px; bottom: 40px;
    display: flex; align-items: center; gap: 10px;
    background: var(--card);
    padding: 8px 12px;
  }
  .back-wordmark .name {
    font-weight: 700; font-size: 30px; color: var(--brand-blue); letter-spacing: -.5px;
  }
  .brand-dot {
    width: 16px; height: 16px; border-radius: 50%; background: var(--brand-orange); flex: none;
  }
  /* Front of card */
  .card-front { left: 500px; top: 478px; }
  .brand-block { position: absolute; left: 34px; top: 44px; }
  .front-wordmark { display: flex; align-items: center; gap: 10px; }
  .front-wordmark .name {
    font-weight: 700; font-size: 25px; color: var(--brand-blue); letter-spacing: -.3px;
  }
  .tagline {
    margin-top: 14px; margin-left: 26px;
    font-weight: 700; font-style: italic; font-size: 19px; color: var(--deep-blue);
  }
  .contact-block { position: absolute; left: 370px; top: 72px; }
  .person-name { font-weight: 700; font-size: 19px; color: var(--deep-blue); line-height: 1.1; }
  .person-title { font-size: 13px; margin-top: 2px; }
  .address { font-size: 13.5px; line-height: 1.35; margin-top: 16px; }
  .contact-list { list-style: none; margin-top: 12px; font-size: 13.5px; line-height: 1.55; }
  .contact-list li { display: flex; align-items: center; gap: 7px; }
  .contact-list svg { width: 12px; height: 12px; fill: var(--deep-blue); flex: none; }
</style>
</head>
<body>
<main class="canvas">
  <section class="card card-back" aria-label="Business card back">
    <div class="fish-pattern" role="img" aria-label="Faint repeating pattern of cartoon fish in pale blue and peach"></div>
    <div class="back-wordmark">
      <span class="brand-dot"></span>
      <span class="name">Tall Pine Computing</span>
    </div>
  </section>

  <section class="card card-front" aria-label="Business card front">
    <div class="brand-block">
      <div class="front-wordmark">
        <span class="brand-dot"></span>
        <span class="name">Tall Pine Computing</span>
      </div>
      <p class="tagline">"rooted in technology"</p>
    </div>

    <div class="contact-block">
      <h1 class="person-name">Daniel Harper</h1>
      <p class="person-title">Managing Director</p>
      <p class="address">12345, Address Goes Here<br>Country Name, 123456.</p>
      <ul class="contact-list">
        <li>
          <svg viewBox="0 0 24 24" aria-hidden="true"><path d="M6.6 10.8a15.1 15.1 0 0 0 6.6 6.6l2.2-2.2a1 1 0 0 1 1-.25 11.4 11.4 0 0 0 3.6.57 1 1 0 0 1 1 1V20a1 1 0 0 1-1 1A17 17 0 0 1 3 4a1 1 0 0 1 1-1h3.5a1 1 0 0 1 1 1c0 1.25.2 2.45.57 3.6a1 1 0 0 1-.25 1z"/></svg>
          055-987 654 321
        </li>
        <li>
          <svg viewBox="0 0 24 24" aria-hidden="true"><path d="M2 5h20v14H2z M2 5l10 8 10-8" fill="none" stroke="#1d6fb8" stroke-width="2.4"/></svg>
          info@tallpinemail.com
        </li>
        <li>
          <svg viewBox="0 0 24 24" aria-hidden="true"><path d="M10 14a4 4 0 0 0 5.6 0l4-4a4 4 0 0 0-5.6-5.6l-1.5 1.5 M14 10a4 4 0 0 0-5.6 0l-4 4a4 4 0 0 0 5.6 5.6l1.5-1.5" fill="none" stroke="#1d6fb8" stroke-width="2.6" stroke-linecap="round"/></svg>
          www.tallpinesite.com
        </li>
      </ul>
    </div>
  </section>
</main>
</body>
</html>
```